Kitchen and custom cabinetry company looking for business card design

We make: * Custom Kitchens, contemporary and traditional kitchens, Vanities, Libraries, Custom Entry Doors, Custom Wine Cellars and Custom Design Furniture. Phone number 555-284-7716. Address: Westhampton NY. Email: KAVRO@mailbox.example Portfolio at: KAVROcabinetry.example I would like moderns fonts and not heavy lines. double side but maybe will use clear plastic. I attached the logo.

Industry/Entity Type

Business

```html
<!DOCTYPE html>
<html lang="en">
<head>
<meta charset="utf-8">
<title>KAVRO Cabinetry Inc. – Business Card</title>
<link rel="stylesheet" href="https://fonts.googleapis.com/css2?family=Cinzel:wght@400;600&family=Josefin+Sans:wght@300;400&display=swap">
<style>
  :root {
    --canvas-bg: #e9e7e4;
    --card-white: #ffffff;
    --card-mist: #e4e4e4;
    --slate-light: #6d6e70;
    --slate-dark: #3f4042;
    --ink: #4a4a4a;
    --ink-soft: #7a7a7a;
    --accent: #e0641f;
    --accent-light: #f08a3c;
    --wave-grey: #c9c9c9;
  }
  * { margin: 0; padding: 0; box-sizing: border-box; }
  html, body { width: 1200px; height: 600px; overflow: hidden; }
  body {
    background: var(--canvas-bg);
    display: flex;
    align-items: center;
    justify-content: center;
    gap: 50px;
    font-family: "Cinzel", Georgia, serif;
  }
  .card {
    position: relative;
    width: 525px;
    height: 300px;
    border-radius: 18px;
    overflow: hidden;
    box-shadow: 0 6px 18px rgba(0,0,0,0.18);
  }

  /* Front side */
  .card-front {
    background: linear-gradient(160deg, var(--card-white) 0%, var(--card-mist) 100%);
    color: var(--ink);
  }
  .front-wave { position: absolute; inset: 0; width: 100%; height: 100%; }
  .brand {
    position: absolute;
    left: 34px;
    top: 58px;
  }
  .brand-name {
    font-family: "Cinzel", Georgia, serif;
    font-weight: 600;
    font-size: 44px;
    letter-spacing: 4px;
    color: var(--slate-light);
    line-height: 1;
  }
  .brand-sub {
    font-family: "Josefin Sans", Arial, sans-serif;
    font-size: 13px;
    letter-spacing: 3px;
    color: var(--slate-light);
    margin-top: 6px;
  }
  .brand-tagline {
    font-family: "Josefin Sans", Arial, sans-serif;
    font-size: 8px;
    letter-spacing: 1.2px;
    color: var(--accent);
    text-transform: uppercase;
    margin-top: 3px;
  }
  .person {
    position: absolute;
    right: 34px;
    top: 30px;
    text-align: right;
  }
  .person-name {
    font-weight: 600;
    font-size: 15px;
    letter-spacing: 1px;
    color: var(--accent);
  }
  .person-role {
    font-size: 9px;
    letter-spacing: 1.5px;
    color: var(--ink-soft);
    margin-top: 3px;
  }
  .divider {
    position: absolute;
    right: 34px;
    top: 78px;
    width: 250px;
    height: 1px;
    background: var(--wave-grey);
  }
  .contact {
    position: absolute;
    right: 34px;
    top: 92px;
    list-style: none;
    text-align: right;
    font-size: 10px;
    line-height: 18px;
    color: var(--ink);
  }
  .contact li { display: flex; align-items: center; justify-content: flex-end; gap: 7px; }
  .contact-icon {
    width: 10px; height: 10px;
    border: 1.2px solid var(--accent);
    border-radius: 2px;
  }
  .contact-icon.filled { background: var(--accent); }
  .services {
    position: absolute;
    left: 40px;
    top: 150px;
    list-style: none;
    font-size: 9.5px;
    line-height: 14px;
    color: var(--ink);
    letter-spacing: 0.4px;
  }
  .services li::before {
    content: "";
    display: inline-block;
    width: 4px; height: 4px;
    border-radius: 50%;
    background: var(--accent);
    margin-right: 7px;
    vertical-align: middle;
  }

  /* Back side */
  .card-back {
    background: linear-gradient(150deg, var(--slate-light) 0%, #58595b 50%, var(--slate-dark) 100%);
    display: flex;
    align-items: center;
    justify-content: center;
  }
  .back-brand { text-align: left; color: #f4f4f4; }
  .back-brand .brand-name { color: #f4f4f4; font-size: 72px; letter-spacing: 6px; }
  .back-brand .brand-sub { color: #f4f4f4; font-size: 20px; letter-spacing: 5px; margin-top: 8px; }
  .back-brand .brand-tagline { color: #d8d8d8; font-size: 11px; letter-spacing: 2px; margin-top: 4px; }
</style>
</head>
<body>
  <section class="card card-front" aria-label="Front of business card">
    <svg class="front-wave" viewBox="0 0 525 300" preserveAspectRatio="none" aria-hidden="true">
      <path d="M0 300 L0 272 C140 272 260 250 340 200 C410 156 460 120 525 110 L525 300 Z" fill="var(--wave-grey)"/>
      <path d="M0 300 L0 284 C150 284 280 268 370 215 C430 180 475 150 525 140 L525 300 Z" fill="var(--accent)"/>
      <path d="M0 300 L0 292 C160 292 300 282 400 235 C450 212 490 190 525 182 L525 300 Z" fill="var(--accent-light)"/>
    </svg>

    <div class="brand">
      <div class="brand-name">KAVRO</div>
      <div class="brand-sub">CABINETRY INC.</div>
      <div class="brand-tagline">Construction of Interior Solutions</div>
    </div>

    <div class="person">
      <div class="person-name">Dario Mendel</div>
      <div class="person-role">MANAGER</div>
    </div>
    <div class="divider"></div>

    <ul class="contact">
      <li>555-284-7716 <span class="contact-icon filled"></span></li>
      <li>KAVRO@mailbox.example <span class="contact-icon filled"></span></li>
      <li>KAVROcabinetry.example <span class="contact-icon"></span></li>
    </ul>

    <ul class="services">
      <li>Custom Kitchens</li>
      <li>Contemporary Kitchens</li>
      <li>Traditional Kitchens</li>
      <li>Vanities</li>
      <li>Libraries</li>
      <li>Custom Entry Doors</li>
      <li>Custom Wine Cellars</li>
      <li>Custom Design Furniture</li>
    </ul>
  </section>

  <section class="card card-back" aria-label="Back of business card">
    <div class="back-brand">
      <div class="brand-name">KAVRO</div>
      <div class="brand-sub">CABINETRY INC.</div>
      <div class="brand-tagline">Construction of Interior Solutions</div>
    </div>
  </section>
</body>
</html>
```